Corporate Business Card

Very professional, Modern, Not to busy, include phone address email, website
(253) 617-4930, 18761 52nd Avenue S, Kent, WA 98047, martin@plumlinegroup.com, varkoworks.com

Target Market(s)

Manufacturing

Industry/Entity Type

Aero, machining, manufacturing, Off road racing

Contact Information for Business Card

Phone, address email, website

```html
<!DOCTYPE html>
<html lang="en">
<head>
<meta charset="utf-8">
<title>Varko Works – Business Card</title>
<link href="https://fonts.googleapis.com/css2?family=Titillium+Web:wght@400;600;700&display=swap" rel="stylesheet">
<style>
  :root {
    --navy: #17356e;
    --red: #d42027;
    --white: #ffffff;
    --ink: #4a4a4f;
    --backdrop: #1c1c1e;
  }
  * { box-sizing: border-box; margin: 0; padding: 0; }
  html, body {
    width: 1200px; height: 1122px; overflow: hidden;
    background: var(--backdrop);
    font-family: "Titillium Web", sans-serif;
  }
  .sheet {
    position: relative; width: 1200px; height: 1122px;
  }
  .card {
    position: absolute; left: 170px; width: 860px; height: 491px;
    border-radius: 34px; overflow: hidden;
  }
  .card--front { top: 45px; background: var(--navy); }
  .card--back { top: 586px; background: var(--white); }

  .brand {
    position: absolute; display: flex; align-items: center; gap: 14px;
    font-weight: 700; letter-spacing: 2px; white-space: nowrap;
  }
  .brand__mark { display: block; }
  .card--front .brand {
    left: 50%; top: 50%; transform: translate(-50%, -50%);
    font-size: 78px; color: var(--white);
  }
  .card--front .brand__mark { width: 26px; height: 26px; background: var(--white); }
  .card--back .brand {
    left: 70px; top: 208px;
    font-size: 48px; color: var(--navy);
  }
  .card--back .brand__mark { width: 18px; height: 18px; background: var(--red); }

  .divider {
    position: absolute; left: 448px; top: 105px;
    width: 2px; height: 270px; background: var(--navy);
  }
  .contact {
    position: absolute; left: 484px; top: 92px;
  }
  .contact__name {
    font-size: 36px; font-weight: 700; color: var(--navy);
    line-height: 1.05; letter-spacing: 0.5px;
  }
  .contact__role {
    font-size: 23px; color: var(--red); margin-bottom: 18px;
  }
  .contact__row {
    display: flex; align-items: flex-start; gap: 14px;
    font-size: 21px; color: var(--ink); line-height: 1.3;
    margin-bottom: 6px;
  }
  .contact__row--gap { margin-top: 10px; }
  .contact__icon { width: 18px; height: 18px; margin-top: 5px; flex: none; }

  .edge-band { position: absolute; left: 0; bottom: 0; width: 860px; height: 22px; }
</style>
</head>
<body>
<div class="sheet">

  <section class="card card--front">
    <div class="brand"><span class="brand__mark"></span>VARKO WORKS</div>
  </section>

  <section class="card card--back">
    <div class="brand"><span class="brand__mark"></span>VARKO WORKS</div>

    <div class="divider"></div>

    <div class="contact">
      <p class="contact__name">DANIEL MERCER</p>
      <p class="contact__role">Managing Director</p>

      <div class="contact__row">
        <svg class="contact__icon" viewBox="0 0 24 24" fill="var(--navy)"><path d="M12 2a7 7 0 0 0-7 7c0 5 7 13 7 13s7-8 7-13a7 7 0 0 0-7-7zm0 9.5A2.5 2.5 0 1 1 12 6.5a2.5 2.5 0 0 1 0 5z"/></svg>
        <span>18761 52nd Avenue S<br>Kent, WA 98047</span>
      </div>
      <div class="contact__row contact__row--gap">
        <svg class="contact__icon" viewBox="0 0 24 24" fill="var(--navy)"><path d="M6.6 10.8a15 15 0 0 0 6.6 6.6l2.2-2.2a1 1 0 0 1 1-.25 11.4 11.4 0 0 0 3.6.57 1 1 0 0 1 1 1V20a1 1 0 0 1-1 1A17 17 0 0 1 3 4a1 1 0 0 1 1-1h3.5a1 1 0 0 1 1 1c0 1.25.2 2.45.57 3.6a1 1 0 0 1-.25 1z"/></svg>
        <span>(253) 617-4930</span>
      </div>
      <div class="contact__row">
        <svg class="contact__icon" viewBox="0 0 24 24" fill="var(--navy)"><path d="M2 5h20v14H2z M2 5l10 8 10-8" stroke="#fff" stroke-width="1.5"/></svg>
        <span>martin@plumlinegroup.com</span>
      </div>
      <div class="contact__row">
        <svg class="contact__icon" viewBox="0 0 24 24"><circle cx="12" cy="12" r="10" fill="none" stroke="var(--navy)" stroke-width="2"/><path d="M2 12h20M12 2c3 3 3 17 0 20M12 2c-3 3-3 17 0 20" fill="none" stroke="var(--navy)" stroke-width="1.5"/></svg>
        <span>www.varkoworks.com</span>
      </div>
    </div>

    <svg class="edge-band" viewBox="0 0 860 22" preserveAspectRatio="none">
      <polygon points="0,0 598,0 590,22 0,22" fill="var(--navy)"/>
      <polygon points="608,0 860,0 860,22 600,22" fill="var(--red)"/>
    </svg>
  </section>

</div>
</body>
</html>
```